Law Firm Website

We are a small California based law firm specializing in business, corporate and litigation matters. We need to have our website redesigned. We are looking for a new and fresh look for our site, keeping in mind that we are a law firm.
What we don't want:
**the traditional "gavel" and "scales of justice" look
**anything too crazy
What we do want:
**sophisticated yet modern and fresh corporate look and feel
**samples of websites we really like:
http://www.tarnwellhope.example
http://www.marrowgate.example/
we also like:
http://www.fenwoodastley.example/
http://www.qz.example/
http://www.brenhollow.example/
http://www.pvdn.example
http://www.nqrlaw.example/
The content will be whatever is currently on our website (www.okabelawgroup.example). We will be selecting the winner based on originality and keeping the above requirements in mind. Please note that the photos that you use will be the ones that we will be using, so choose wisely because the photos will make a difference.
Target Market(s)
Corporate clients
Industry/Entity Type
Law Firm
Look and feel

```html
<!DOCTYPE html>
<html lang="en">
<head>
<meta charset="utf-8">
<title>Okabe Law Group, LLP — Law Center</title>
<link rel="stylesheet" href="https://fonts.googleapis.com/css2?family=Oswald:wght@600&family=Roboto+Condensed:wght@400;700&family=Roboto:wght@300;400&display=swap">
<style>
  :root {
    --ink: #000000;
    --paper: #ffffff;
    --text: #3a3a3a;
    --rule: #cfcfcf;
    --brand-blue: #2f86e0;
    --footer-head: #9a9a9a;
    --footer-text: #8a8a8a;
    --photo-top: #9a9a9a;
    --photo-mid: #5e5e5e;
    --photo-bottom: #2f2f2f;
  }
  * { box-sizing: border-box; margin: 0; padding: 0; }
  html, body { width: 1200px; height: 923px; overflow: hidden; background: var(--paper); }
  body { position: relative; font-family: "Roboto", Arial, sans-serif; color: var(--text); }
  a { color: inherit; text-decoration: none; }

  .top-bar { position: absolute; left: 0; top: 0; width: 1200px; height: 6px; background: var(--ink); }

  .phone-tab {
    position: absolute; left: 889px; top: 0; width: 132px; height: 41px;
    background: var(--ink); border-radius: 0 0 7px 7px;
    display: flex; align-items: center; justify-content: center; gap: 8px;
    color: var(--paper); font-family: "Roboto", Arial, sans-serif; font-size: 14px;
  }

  .brand { position: absolute; left: 172px; top: 35px; width: 210px; }
  .brand-mark { display: block; width: 96px; height: 97px; margin-left: 48px; background: var(--brand-blue); }
  .brand-name {
    display: block; margin-top: 2px; white-space: nowrap;
    font-family: "Oswald", "Arial Narrow", sans-serif; font-weight: 600; font-size: 22px;
    color: var(--ink); letter-spacing: 0.2px;
  }

  .main-nav { position: absolute; left: 432px; top: 78px; width: 768px; height: 25px; border-bottom: 2px solid var(--rule); }
  .main-nav a {
    position: absolute; top: 6px; font-family: "Roboto Condensed", Arial, sans-serif;
    font-weight: 700; font-size: 12px; color: var(--ink); letter-spacing: 0.3px;
  }
  .nav-sep { position: absolute; top: 16px; width: 1px; height: 8px; background: var(--rule); }

  .hero-title {
    position: absolute; left: 168px; top: 282px;
    font-family: "Roboto Condensed", "Arial Narrow", sans-serif; font-weight: 700;
    font-size: 62px; line-height: 1; color: var(--ink); letter-spacing: -0.6px;
  }
  .hero-text {
    position: absolute; left: 170px; top: 357px; width: 300px;
    font-family: "Roboto", Arial, sans-serif; font-weight: 300; font-size: 21px; line-height: 29.5px; color: var(--text);
  }
  .cta {
    position: absolute; left: 170px; top: 522px; width: 283px; height: 41px;
    background: var(--ink); color: var(--paper);
    display: flex; align-items: center; justify-content: space-between; padding: 0 16px;
    font-family: "Roboto", Arial, sans-serif; font-size: 13px; letter-spacing: 0.1px;
  }

  .team-photo {
    position: absolute; left: 553px; top: 224px; width: 445px; height: 486px;
    background: linear-gradient(180deg, var(--photo-top) 0%, var(--photo-mid) 55%, var(--photo-bottom) 100%);
  }

  .site-footer { position: absolute; left: 0; top: 755px; width: 1200px; height: 168px; background: var(--ink); }
  .footer-col { position: absolute; top: 31px; }
  .footer-col h3 {
    font-family: "Roboto Condensed", Arial, sans-serif; font-weight: 700; font-size: 13px;
    color: var(--footer-head); margin-bottom: 12px; letter-spacing: 0.2px;
  }
  .footer-col li { list-style: none; font-size: 11px; line-height: 21px; color: var(--footer-text); }
  .footer-col li::before { content: "//"; margin-right: 8px; }
  .footer-brand { position: absolute; left: 785px; top: 30px; }
  .footer-brand h2 {
    font-family: "Roboto", Arial, sans-serif; font-weight: 300; font-size: 28px; color: var(--footer-head);
    letter-spacing: 0.5px; margin-bottom: 20px;
  }
  .footer-brand p { font-size: 11px; line-height: 14px; color: #6f6f6f; }
</style>
</head>
<body>
  <div class="top-bar"></div>

  <div class="phone-tab">
    <svg width="14" height="16" viewBox="0 0 14 16" aria-hidden="true">
      <path d="M3 1 L6 1 L7 5 L5 6.5 C6 9 7.5 10.5 9.5 11.5 L11 9.5 L14 10.5 L14 14 C14 15 13 15.5 12 15.5 C6 15 1 10 0.5 3.5 C0.5 2 1.5 1 3 1 Z" fill="#ffffff"/>
    </svg>
    <span>000-000-000</span>
  </div>

  <header class="brand">
    <span class="brand-mark"></span>
    <span class="brand-name">Okabe Law Group, LLP</span>
  </header>

  <nav class="main-nav">
    <a href="#" style="left:211px">HOME</a>
    <span class="nav-sep" style="left:264px"></span>
    <a href="#" style="left:293px">ABOUT US</a>
    <span class="nav-sep" style="left:371px"></span>
    <a href="#" style="left:401px">SERVICES</a>
    <span class="nav-sep" style="left:479px"></span>
    <a href="#" style="left:502px">CONTACT US</a>
  </nav>

  <h1 class="hero-title">LAW CENTER</h1>
  <p class="hero-text">Lorem Ipsum is simply dummy<br>text of the printing and typeset-<br>ting industry. Lorem Ipsum has<br>been the industry's</p>
  <a class="cta" href="#">
    <span>CONTACT US FOR QUICK ADVICE</span>
    <svg width="26" height="14" viewBox="0 0 26 14" aria-hidden="true">
      <path d="M0 7 H23 M17 1.5 L23.5 7 L17 12.5" stroke="#ffffff" stroke-width="2.2" fill="none"/>
    </svg>
  </a>

  <div class="team-photo" role="img" aria-label="Black and white photo of four attorneys in dark suits, one seated on a stool, the others standing"></div>

  <footer class="site-footer">
    <div class="footer-col" style="left:170px">
      <h3>QUICK LINKS</h3>
      <ul><li>Home</li><li>Services</li><li>Contact us</li><li>Privacy policy</li></ul>
    </div>
    <div class="footer-col" style="left:477px">
      <h3>SOCIAL</h3>
      <ul><li>Friendbook</li><li>Chirper</li><li>WorkNet</li><li>Blog</li></ul>
    </div>
    <div class="footer-brand">
      <h2>LAW CENTER</h2>
      <p>417 Larchmere Ave, Suite 300 Calden, WA 98000<br>P.O Box 212 // &nbsp;Phone: 000-000-000</p>
    </div>
  </footer>
</body>
</html>
```